Business Card Design

New business card design

Target Market(s)

Residential & Commercial Property Managers

Industry/Entity Type

Plumbing Services

Contact Information for Business Card

Name - Rowan Keddle, title - Director, Phone Number - 0431 286 517, email - rowan@tbk-plumbing.com.au, Company ABN - 73 215 904 386,

Font styles to use
Sans Serif

Colors
0054AA
0677BA
7BADD7
CADEEF
E8F1F8

```html
<!DOCTYPE html>
<html lang="en">
<head>
<meta charset="utf-8">
<title>tbk plumbing services — Business Card</title>
<link rel="stylesheet" href="https://fonts.googleapis.com/css2?family=Montserrat:wght@400;500;700&display=swap">
<style>
  :root {
    --backdrop: #d9d4cc;
    --card-white: #ffffff;
    --brand-blue: #2ba6e0;
    --ink: #1d2530;
    --ink-soft: #2a2f36;
  }
  * { box-sizing: border-box; margin: 0; padding: 0; }
  html, body { width: 900px; height: 1200px; overflow: hidden; }
  body {
    background: var(--backdrop);
    font-family: "Montserrat", sans-serif;
    color: var(--ink);
    position: relative;
  }
  .card {
    position: absolute;
    border-radius: 22px;
    overflow: hidden;
    box-shadow: 0 6px 14px rgba(0,0,0,0.35);
  }
  .card-front { left: 80px; top: 131px; width: 742px; height: 440px; background: var(--card-white); }
  .card-back  { left: 78px; top: 638px; width: 744px; height: 440px; background: var(--brand-blue); }

  .brand-name {
    font-family: "Montserrat", sans-serif;
    font-weight: 500;
    color: var(--ink);
    white-space: nowrap;
    letter-spacing: 1px;
  }
  .card-front .brand-name { position: absolute; left: 40px; top: 40px; font-size: 36px; }
  .card-back .brand-name {
    position: absolute; left: 0; right: 0; top: 188px;
    text-align: center; font-size: 52px;
  }

  .accent-disc {
    position: absolute; left: 405px; top: 110px;
    width: 320px; height: 320px; border-radius: 50%;
    background: var(--brand-blue);
  }

  .contact-block { position: absolute; left: 39px; top: 160px; }
  .person-name { font-size: 25px; font-weight: 700; line-height: 1; }
  .person-title { font-size: 15px; margin-top: 9px; color: var(--ink-soft); }
  .address { font-size: 16px; line-height: 20px; margin-top: 28px; color: var(--ink-soft); }
  .contact-list { list-style: none; margin-top: 16px; }
  .contact-list li {
    display: flex; align-items: center; gap: 10px;
    font-size: 15.5px; height: 31px; color: var(--ink-soft);
  }
  .contact-list svg { width: 18px; height: 18px; fill: var(--ink); flex: none; }
  .abn { font-size: 15.5px; margin-top: 10px; color: var(--ink-soft); }
  .abn strong { font-weight: 700; color: var(--ink); }
</style>
</head>
<body>
  <section class="card card-front">
    <div class="brand-name">tbk plumbing services</div>
    <div class="accent-disc" aria-hidden="true"></div>
    <div class="contact-block">
      <h1 class="person-name">Rowan Keddle</h1>
      <p class="person-title">Director</p>
      <p class="address">48 Harrow Creek Road<br>Ballarat, VIC 3350</p>
      <ul class="contact-list">
        <li>
          <svg viewBox="0 0 24 24" aria-hidden="true"><path d="M6.6 10.8a15.1 15.1 0 0 0 6.6 6.6l2.2-2.2a1 1 0 0 1 1-.25 11.4 11.4 0 0 0 3.6.57 1 1 0 0 1 1 1V20a1 1 0 0 1-1 1A17 17 0 0 1 3 4a1 1 0 0 1 1-1h3.5a1 1 0 0 1 1 1c0 1.25.2 2.45.57 3.57a1 1 0 0 1-.25 1z"/></svg>
          0431 286 517
        </li>
        <li>
          <svg viewBox="0 0 24 24" aria-hidden="true"><path d="M3 6h18v12H3z" fill="none"/><path d="M3 5h18a1 1 0 0 1 1 1v.4l-10 6.2L2 6.4V6a1 1 0 0 1 1-1zm-1 3.7 10 6.2 10-6.2V18a1 1 0 0 1-1 1H3a1 1 0 0 1-1-1z"/></svg>
          rowan@tbk-plumbing.com.au
        </li>
        <li>
          <svg viewBox="0 0 24 24" aria-hidden="true"><path d="M12 2a10 10 0 1 0 0 20 10 10 0 0 0 0-20zm6.9 6h-3a15.7 15.7 0 0 0-1.4-3.6A8 8 0 0 1 18.9 8zM12 4c.8 1.2 1.5 2.5 1.9 4h-3.8c.4-1.5 1.1-2.8 1.9-4zM4.3 14a8 8 0 0 1 0-4h3.4a16 16 0 0 0 0 4zm.8 2h3a15.7 15.7 0 0 0 1.4 3.6A8 8 0 0 1 5.1 16zm3-8h-3a8 8 0 0 1 4.4-3.6A15.7 15.7 0 0 0 8.1 8zM12 20c-.8-1.2-1.5-2.5-1.9-4h3.8c-.4 1.5-1.1 2.8-1.9 4zm2.3-6H9.7a14.6 14.6 0 0 1 0-4h4.6a14.6 14.6 0 0 1 0 4zm.2 5.6a15.7 15.7 0 0 0 1.4-3.6h3a8 8 0 0 1-4.4 3.6zm1.8-5.6a16 16 0 0 0 0-4h3.4a8 8 0 0 1 0 4z"/></svg>
          www.tbk-plumbing.com.au
        </li>
      </ul>
      <p class="abn"><strong>ABN</strong> - 73 215 904 386</p>
    </div>
  </section>

  <section class="card card-back">
    <div class="brand-name">tbk plumbing services</div>
  </section>
</body>
</html>
```